wealth management firm, professional group, new model

we have a logo that works but we need a card, white background using our colors...clean look

our tag line if can be used in

The Bridge From Client to Owner

```html
<!DOCTYPE html>
<html lang="en">
<head>
<meta charset="UTF-8">
<title>Arvel Wealth Partners – Business Card</title>
<link rel="stylesheet" href="https://fonts.googleapis.com/css2?family=Montserrat:wght@300;400;500;800&display=swap">
<style>
  :root {
    --navy: #0d1f45;
    --navy-deep: #020a22;
    --navy-glow: #14305a;
    --paper: #ffffff;
    --paper-shade: #ececec;
    --ink-soft: #3a3f4a;
    --ground: #e6e7ea;
  }
  * { margin: 0; padding: 0; box-sizing: border-box; }
  html, body {
    width: 1200px;
    height: 900px;
    overflow: hidden;
    background: var(--ground);
    font-family: "Montserrat", sans-serif;
  }
  .canvas {
    width: 1200px;
    height: 900px;
    display: flex;
    flex-direction: column;
    align-items: center;
    justify-content: center;
    gap: 56px;
  }
  .card {
    width: 580px;
    height: 330px;
    border-radius: 30px;
    display: flex;
    flex-direction: column;
    align-items: center;
    justify-content: center;
    box-shadow: 0 10px 28px rgba(0, 0, 0, 0.18);
  }
  .card--front {
    background: radial-gradient(ellipse at 50% 50%, var(--navy-glow) 0%, #0a1d40 45%, var(--navy-deep) 100%);
    color: var(--paper);
  }
  .card--back {
    background: linear-gradient(120deg, var(--paper-shade) 0%, var(--paper) 55%, var(--paper) 100%);
    color: var(--navy);
    justify-content: flex-start;
    padding-top: 46px;
  }
  .brand {
    display: flex;
    flex-direction: column;
    align-items: center;
  }
  .brand__name {
    font-weight: 300;
    font-size: 34px;
    letter-spacing: 0.62em;
    margin-right: -0.62em;
    line-height: 1;
  }
  .brand__sub {
    font-weight: 300;
    font-size: 11px;
    letter-spacing: 0.28em;
    margin-right: -0.28em;
    margin-top: 14px;
  }
  .card--back .brand__name { font-size: 30px; }
  .card--back .brand__sub { font-size: 10px; margin-top: 12px; }
  .holder {
    margin-top: 26px;
    text-align: center;
  }
  .holder__name {
    font-weight: 800;
    font-size: 15px;
    letter-spacing: -0.01em;
    color: var(--navy);
  }
  .holder__role {
    font-weight: 400;
    font-size: 12px;
    color: var(--ink-soft);
    margin-top: 1px;
  }
  .contact {
    margin-top: 20px;
    text-align: center;
    font-size: 11.5px;
    font-weight: 400;
    line-height: 1.65;
    color: var(--ink-soft);
  }
  .contact__label {
    font-weight: 500;
    color: var(--navy);
  }
</style>
</head>
<body>
  <main class="canvas">
    <section class="card card--front" aria-label="Card front">
      <div class="brand">
        <span class="brand__name">ARVEL</span>
        <span class="brand__sub">WEALTH PARTNERS</span>
      </div>
    </section>

    <section class="card card--back" aria-label="Card back">
      <div class="brand">
        <span class="brand__name">ARVEL</span>
        <span class="brand__sub">WEALTH PARTNERS</span>
      </div>
      <div class="holder">
        <p class="holder__name">DANIEL REYES</p>
        <p class="holder__role">Director</p>
      </div>
      <div class="contact">
        <p><span class="contact__label">P.</span> 300-415-7280</p>
        <p><span class="contact__label">E.</span> info@arvelwealth.com | www.arvelwealth.com</p>
        <p>12 Harbor Street, Lakeview 4021</p>
      </div>
    </section>
  </main>
</body>
</html>
```